Copperbend Blazeworks Website Design

I am looking for a website design ( Home page and inner template page ) in a .psd format. The home page needs to have a large hero image what will function as a "slider", and have some highlight graphical areas/links to the following links "Public & Municipal Events", "Corporate Events", "Special Events". The main navigation needs to have the following nav links "gallery", "home", "about", "services" and "contact". Unfortunately the client does not have any nice hi-rez images ( this is a company that specializes is large fireworks displays ) so please use stock photography sample images from snapvaultpics since we have an account there an can purchase the photos if our client wants to use them. Our current full time graphic artist has been with us for a long time so we are looking at artflockhub as a way to add a fresh approach to design and possibly find someone we can work with regularly. Here is a few designs that in the way we display them for our clients for approval. As you can see there are a couple that don't have their own images so they are utilizing the before mentioned snapvaultpics samples. On the plus side we did manage to get their logo in a .ai format. We have our team for handling the conversion from design to html.

http://reedfoxbuildstudio.com/dev/

```html
<!DOCTYPE html>
<html lang="en">
<head>
<meta charset="utf-8">
<title>Copperbend Blazeworks</title>
<link href="https://fonts.googleapis.com/css2?family=Roboto+Slab:wght@300;400;700&family=Montserrat:wght@400;500;600&family=Mulish:wght@400&display=swap" rel="stylesheet">
<style>
:root{
  --blue:#3fa3de;
  --blue-deep:#1f80c1;
  --ink:#111;
  --text:#444;
  --grey-panel:#ebebeb;
  --white:#fff;
  --bar:#d6e9f6;
}
*{margin:0;padding:0;box-sizing:border-box}
html,body{width:1200px;height:2562px;overflow:hidden;background:var(--white)}
body{position:relative;font-family:"Montserrat",sans-serif;color:var(--text)}
.abs{position:absolute}
.top-stripe{left:0;top:0;width:1200px;height:6px;background:var(--blue)}
.site-header{left:0;top:6px;width:1200px;height:85px;background:var(--white)}
.brand{left:96px;top:0;width:150px;height:110px;border-radius:0 0 75px 75px;background:var(--white);display:flex;align-items:center;justify-content:center;text-align:center;font-family:"Roboto Slab",serif;font-weight:400;font-size:19px;line-height:22px;color:var(--ink);z-index:3}
.main-nav{right:106px;top:33px;display:flex;gap:41px;font-family:"Roboto Slab",serif;font-size:16px;letter-spacing:.5px;color:var(--ink)}
.main-nav .active{color:var(--blue)}
.hero{left:0;top:91px;width:1200px;height:554px;background:radial-gradient(ellipse at 70% 30%,#c8445e 0%,transparent 55%),radial-gradient(ellipse at 25% 25%,#a0693a 0%,transparent 50%),linear-gradient(180deg,#3a2a56 0%,#7a3a66 45%,#b0556a 75%,#3a2030 100%)}
.hero-title{left:0;top:190px;width:1200px;text-align:center;font-family:"Roboto Slab",serif;font-size:58px;color:var(--white);letter-spacing:1px}
.hero-title .light{font-weight:300}
.hero-title .bold{font-weight:700}
.hero-sub{left:300px;top:267px;width:600px;text-align:center;font-size:15px;line-height:24px;font-weight:500;color:var(--white);letter-spacing:.3px}
.btn{display:flex;align-items:center;justify-content:center;width:163px;height:43px;border-radius:22px;font-size:15px;font-weight:500;letter-spacing:1.5px}
.hero .btn{left:519px;top:330px;background:var(--blue);color:var(--white)}
.arrow{top:243px;width:62px;height:62px;border:1.5px solid var(--white);border-radius:50%}
.arrow svg{position:absolute;left:19px;top:19px}
.dots{left:580px;top:512px;display:flex;gap:6px;align-items:center}
.dots span{width:8px;height:8px;border-radius:50%;border:1px solid var(--white)}
.dots .on{width:11px;height:11px;background:var(--blue);border:none}
.section-title{left:0;width:1200px;text-align:center;font-family:"Roboto Slab",serif;font-weight:700;font-size:36px;letter-spacing:1.5px;color:var(--ink)}
.rule{left:563px;width:74px;height:3px;background:var(--blue)}
.panel{width:603px;height:321px}
.panel.grey{background:var(--grey-panel)}
.panel.white{background:var(--white)}
.panel h3{position:absolute;font-family:"Roboto Slab",serif;font-weight:400;font-size:21px;letter-spacing:1.2px;color:var(--ink)}
.panel p{position:absolute;width:430px;font-size:15px;line-height:24px;letter-spacing:.3px;color:var(--text)}
.panel a{position:absolute;font-family:"Roboto Slab",serif;font-size:14px;letter-spacing:.8px;color:var(--blue-deep);text-decoration:underline}
.photo{width:584px}
.split{left:603px;top:818px;width:13px;height:967px;background:var(--blue)}
.about{left:0;top:1785px;width:1200px;height:415px;background:linear-gradient(180deg,#2287c8,#1d7cbd)}
.about-title{left:0;top:80px;width:1200px;text-align:center;font-family:"Roboto Slab",serif;font-size:36px;letter-spacing:1.5px;color:var(--white)}
.about-title b{font-weight:700}
.about-title span{font-weight:300}
.about .rule{top:134px;background:var(--white)}
.about p{left:200px;top:160px;width:800px;text-align:center;font-size:15.5px;line-height:24px;font-weight:500;color:var(--white)}
.about .btn{left:519px;top:284px;background:var(--white);color:var(--blue)}
.footer-brand{left:110px;top:2340px;width:230px;text-align:center;font-family:"Roboto Slab",serif;font-weight:400;font-size:30px;line-height:34px;color:var(--ink)}
.social{top:2450px;width:54px;height:54px;border:1px solid #333;border-radius:50%}
.footer-col h4{font-family:"Roboto Slab",serif;font-weight:400;font-size:20px;letter-spacing:.5px;color:var(--ink);margin-bottom:22px}
.footer-col li{list-style:none;font-family:"Mulish",sans-serif;font-size:12.5px;line-height:28px;color:#222}
.contact-item{display:flex;gap:14px;font-family:"Mulish",sans-serif;font-size:12.5px;line-height:22px;color:#222;margin-bottom:14px}
.contact-item svg{flex:none;margin-top:4px}
.to-top{left:1137px;top:2488px;width:32px;height:32px;border-radius:50%;background:var(--blue)}
.to-top svg{position:absolute;left:10px;top:11px}
.copyright{left:0;top:2532px;width:1200px;height:30px;background:var(--bar);text-align:center;font-family:"Mulish",sans-serif;font-size:13px;line-height:30px;color:#222}
</style>
</head>
<body>
<div class="abs top-stripe"></div>
<header class="abs site-header">
  <nav class="abs main-nav">
    <span class="active">Home</span><span>About</span><span>Services</span><span>Gallery</span><span>Contact</span>
  </nav>
</header>
<div class="abs brand">Copperbend<br>Blazeworks</div>

<section class="abs hero" role="img" aria-label="Fireworks bursting over a night sky with a family silhouetted watching">
  <h1 class="abs hero-title"><span class="light">Copperbend</span> <span class="bold">Blazeworks</span></h1>
  <p class="abs hero-sub">Perspiciatis unde omnis iste natus error sit voluptatem accusantium doloremque laudantium, totam rem aperiam.</p>
  <div class="abs btn">GET STARTED</div>
  <div class="abs arrow" style="left:29px"><svg width="24" height="24" viewBox="0 0 24 24" fill="none" stroke="#fff" stroke-width="2"><path d="M20 12H4M10 6l-6 6 6 6"/></svg></div>
  <div class="abs arrow" style="left:1109px"><svg width="24" height="24" viewBox="0 0 24 24" fill="none" stroke="#fff" stroke-width="2"><path d="M4 12h16M14 6l6 6-6 6"/></svg></div>
  <div class="abs dots"><span class="on"></span><span></span><span></span></div>
</section>

<h2 class="abs section-title" style="top:720px">CATEGORY</h2>
<div class="abs rule" style="top:774px"></div>

<div class="abs panel grey" style="left:0;top:818px">
  <h3 style="left:111px;top:58px">PUBLIC &amp; MUNICIPAL EVENTS</h3>
  <p style="left:111px;top:100px">Perspiciatis unde omnis iste natus error sit voluptatem accusantium doloremque laudantium, totam rem aperiam, eaque ipsa quae ab illo inventore veritatis et quasi architecto beatae vitae dicta sunt explicabo. Nemo enim ipsam voluptatem.</p>
  <a style="left:111px;top:246px">READ MORE</a>
</div>
<div class="abs photo" role="img" aria-label="Fireworks over a lit bridge and city skyline at night" style="left:616px;top:818px;height:325px;background:linear-gradient(160deg,#1c2350 0%,#3a3470 40%,#8a5a4a 65%,#1a3a4a 100%)"></div>

<div class="abs photo" role="img" aria-label="Sparkler candle burning on a cake at a party" style="left:0;top:1138px;width:603px;height:322px;background:radial-gradient(ellipse at 50% 35%,#f5b050 0%,#8a3c1a 35%,#1a0e10 75%)"></div>
<div class="abs panel white" style="left:616px;top:1138px;width:584px">
  <h3 style="left:71px;top:58px">CORPORATE EVENTS</h3>
  <p style="left:71px;top:100px">Perspiciatis unde omnis iste natus error sit voluptatem accusantium doloremque laudantium, totam rem aperiam, eaque ipsa quae ab illo inventore veritatis et quasi architecto beatae vitae dicta sunt explicabo. Nemo enim ipsam voluptatem.</p>
  <a style="left:71px;top:246px">READ MORE</a>
</div>

<div class="abs panel grey" style="left:0;top:1460px;height:325px">
  <h3 style="left:110px;top:58px">SPECIAL EVENTS</h3>
  <p style="left:111px;top:100px">Perspiciatis unde omnis iste natus error sit voluptatem accusantium doloremque laudantium, totam rem aperiam, eaque ipsa quae ab illo inventore veritatis et quasi architecto beatae vitae dicta sunt explicabo. Nemo enim ipsam voluptatem.</p>
  <a style="left:111px;top:246px">READ MORE</a>
</div>
<div class="abs photo" role="img" aria-label="Colourful fireworks above downtown towers at night" style="left:616px;top:1460px;height:325px;background:linear-gradient(150deg,#a8304a 0%,#2a2250 45%,#1a2a5a 75%,#c04060 100%)"></div>

<div class="abs split"></div>

<section class="abs about" role="img" aria-label="Blue band with faint fireworks texture">
  <h2 class="abs about-title"><b>ABOUT</b> <span>US</span></h2>
  <div class="abs rule"></div>
  <p class="abs">Perspiciatis unde omnis iste natus error sit voluptatem accusantium doloremque laudantium, totam rem aperiam, eaque ipsa quae ab illo inventore veritatis et quasi architecto beatae vitae dicta sunt explicabo. Nemo enim ipsam voluptatem quia voluptas sit  numquam eius modi tempora incidunt ut labore et dolore magnam aliquam</p>
  <div class="abs btn">READ MORE</div>
</section>

<footer>
  <div class="abs footer-brand">Copperbend<br>Blazeworks</div>
  <div class="abs social" style="left:134px" aria-label="Social profile"></div>
  <div class="abs social" style="left:198px" aria-label="Social profile"></div>
  <div class="abs social" style="left:261px" aria-label="Social profile"></div>

  <div class="abs footer-col" style="left:412px;top:2284px">
    <h4>Quick Links</h4>
    <ul><li>Home</li><li>About</li><li>Services</li><li>Gallery</li><li>Contact</li></ul>
  </div>
  <div class="abs footer-col" style="left:597px;top:2284px">
    <h4>Links</h4>
    <ul><li>Frequently Asked Questions</li><li>Terms &amp; Conditions</li><li>Privacy Policy</li><li>Site Map</li></ul>
  </div>
  <div class="abs footer-col" style="left:822px;top:2284px;width:300px">
    <h4>Contact Us</h4>
    <div class="contact-item"><svg width="14" height="16" viewBox="0 0 14 16"><path d="M7 0a6 6 0 0 0-6 6c0 4.5 6 10 6 10s6-5.5 6-10a6 6 0 0 0-6-6zm0 8.5A2.5 2.5 0 1 1 7 3.5a2.5 2.5 0 0 1 0 5z" fill="#3fa3de"/></svg><span>Address: 418 Tamarack Bend Road,<br>Duluth Falls, USA 55802</span></div>
    <div class="contact-item"><svg width="14" height="14" viewBox="0 0 24 24"><path d="M6.6 10.8a15 15 0 0 0 6.6 6.6l2.2-2.2a1 1 0 0 1 1-.25 11.4 11.4 0 0 0 3.6.57 1 1 0 0 1 1 1V20a1 1 0 0 1-1 1A17 17 0 0 1 3 4a1 1 0 0 1 1-1h3.5a1 1 0 0 1 1 1c0 1.25.2 2.45.57 3.57a1 1 0 0 1-.25 1z" fill="#3fa3de"/></svg><span>Phone: 0198-765-432</span></div>
    <div class="contact-item"><svg width="16" height="12" viewBox="0 0 16 12"><rect width="16" height="12" rx="1" fill="#3fa3de"/><path d="M1 1l7 6 7-6" stroke="#fff" stroke-width="1.3" fill="none"/></svg><span>Email: hello@copperbendblaze.com</span></div>
  </div>

  <div class="abs to-top"><svg width="12" height="8" viewBox="0 0 12 8" fill="none" stroke="#fff" stroke-width="2"><path d="M1 7l5-5 5 5"/></svg></div>
  <div class="abs copyright">Copyright © 2021 - All rights reserved</div>
</footer>
</body>
</html>
```